Harvest Gateway Fellowship Ministries needs a fresh new web design

We are an up and coming multicultural church that aims to bring people into a life changing encounter with God. We need a fresh and inviting website in order to increase our internet presence and make us easier to connect with.
Here are some of the basic requirements for the site:
• Clearly displayed address, service times, and contact info
• A staff profile page
• An area for a calendar with upcoming events and their details
• Social media buttons
• Group pages for the different ministries (youth, children’s church, men, etc…)
• An area for donations and eCommerce
• A resources page for assorted media (podcasts, sermons, videos, etc.…)
• An area for prayer requests.

```html
<!DOCTYPE html>
<html lang="en">
<head>
<meta charset="utf-8">
<title>Harvest Gateway Fellowship Ministries – Resource Center</title>
<link href="https://fonts.googleapis.com/css2?family=Lato:wght@300;400;700&display=swap" rel="stylesheet">
<style>
:root{
  --royal:#1e169c;
  --royal-deep:#19128a;
  --gold:#e2bd12;
  --gold-text:#d9ae0e;
  --ink:#333;
  --muted:#8a8a8a;
  --page:#f1f1f1;
  --card:#fff;
  --line:#e3e3e3;
  --player:#3b3b3b;
}
*{box-sizing:border-box;margin:0;padding:0}
html,body{width:821px;height:1200px;overflow:hidden}
body{font-family:"Lato",Arial,sans-serif;color:var(--ink);background:var(--page);position:relative}
a{color:inherit;text-decoration:none}

.topbar{height:27px;background:var(--royal);color:#fff;display:flex;align-items:center;justify-content:space-between;padding:0 68px;font-size:8.5px}
.topbar__tagline{font-size:9px}
.schedule{display:flex;align-items:center;gap:8px}
.schedule__label{font-size:9.5px}
.schedule__times{border-left:1px solid #fff;padding-left:6px;line-height:10px;font-size:8px}

.header{height:78px;background:#fff;position:relative}
.brand{position:absolute;left:68px;top:42px;display:flex;align-items:center;gap:6px;width:170px}
.brand__dot{width:30px;height:30px;border-radius:50%;background:var(--royal);flex:none}
.brand__name{font-size:11px;font-weight:700;color:var(--royal);line-height:13px}
.info{position:absolute;top:16px;text-align:right;font-size:9px;line-height:11px;color:#555}
.info h3{font-size:11px;font-weight:700;color:#444;margin-bottom:5px}
.info .more{color:var(--gold-text);font-size:8px;display:block;margin-top:1px}
.info--donate{right:429px;width:120px}
.info--prayer{right:236px;width:180px}
.info--address{right:115px;width:110px}
.divider{position:absolute;top:18px;width:1px;height:42px;background:#ccc}
.social{position:absolute;right:68px;top:46px;display:flex;flex-direction:column;gap:3px}
.social span{width:19px;height:19px;border-radius:50%;background:#bdbdbd;display:block}

.nav{height:28px;background:var(--gold);display:flex;align-items:center;padding:0 68px}
.nav a{font-size:9.5px;color:#3a3000;padding:0 16px;border-left:1px solid rgba(0,0,0,.12);line-height:14px}
.nav a:first-child{border-left:0;padding-left:11px}

.banner{height:69px;background:linear-gradient(90deg,#3a2a08,#6b5117 40%,#4a3810 70%,#2e2106);padding:19px 68px 0;color:#fff}
.crumbs{font-size:9px}
.banner h1{font-size:18px;font-weight:700;margin-top:2px}

.filter{position:absolute;left:75px;top:239px;display:flex;align-items:center;font-size:14px;color:#555}
.filter__label{font-size:9px;color:var(--muted);margin-right:8px}
.filter a{padding:0 12px;border-left:1px solid #ccc;line-height:13px}
.filter a.active{color:var(--gold);border-left:0;padding-left:0}

.column{position:absolute;top:271px;width:212px;display:flex;flex-direction:column;gap:8px}
.column--left{left:75px}
.column--right{left:294px}
.card{background:var(--card);box-shadow:0 1px 2px rgba(0,0,0,.08);display:flex;flex-direction:column}
.card--audio{height:172px}
.card--video{height:319px}
.card__media{height:160px;background:linear-gradient(180deg,#3b3480 0%,#6a5aa0 40%,#b07aa6 70%,#e9b890 100%)}
.card__body{flex:1;text-align:center;padding:30px 14px 0}
.card--video .card__body{padding-top:16px}
.card__title{font-size:16px;font-weight:300;color:#333}
.card__type{font-size:10px;color:var(--muted);margin-bottom:12px}
.card__artist{font-size:9px;font-weight:700;color:#444;margin:1px 0 12px}
.card__text{font-size:8.7px;line-height:13.5px;color:#555}
.card__foot{height:25px;border-top:1px solid var(--line);margin:0 14px;display:flex;align-items:center;justify-content:space-between;font-size:7.5px;color:#777}
.share{display:flex;align-items:center;gap:2px;color:#bbb}
.share i{width:14px;height:14px;border-radius:50%;background:#ddd;display:block}

.player{height:20px;background:var(--player);display:flex;align-items:center;padding:0 7px;gap:8px;border-bottom:1px solid #222}
.player__play{width:0;height:0;border-left:6px solid #ddd;border-top:3.5px solid transparent;border-bottom:3.5px solid transparent}
.player__track{flex:1;height:4px;background:#666;margin-left:8px;position:relative}
.player__track::before{content:"";position:absolute;left:0;top:0;bottom:0;width:65%;background:var(--gold)}
.player__vol{width:1px;height:20px;background:#222}
.player__volbar{width:26px;height:4px;background:#666;position:relative}
.player__volbar::before{content:"";position:absolute;left:0;top:0;bottom:0;width:70%;background:var(--gold)}

.archive{position:absolute;left:540px;top:239px;width:206px}
.archive h2{font-size:17px;font-weight:300;color:var(--gold);border-bottom:1px solid var(--gold);padding-bottom:3px;letter-spacing:.2px}
.archive li{list-style:none;font-size:13.5px;color:#555;height:37.5px;line-height:37.5px;border-bottom:1px solid #e4e4e4}
.archive li span{color:var(--muted)}
.archive li.current{color:var(--gold)}

.footer{position:absolute;left:0;top:993px;width:821px;height:207px;background:var(--royal);color:#fff}
.footer__col{position:absolute;top:29px;font-size:9px;line-height:12.5px;color:#cfcdf0}
.footer__col h4{font-size:12.5px;font-weight:300;color:#fff;margin-bottom:8px;letter-spacing:.2px}
.footer__col--contact{left:68px}
.footer__col--serve{left:220px}
.footer__col--news{left:410px}
.footer__col--connect{left:600px;width:160px}
.contact-line{display:flex;align-items:center;gap:8px;margin-top:6px;font-size:9.5px}
.serve-lists{display:flex;gap:14px}
.serve-lists ul{list-style:none}
.serve-lists li{margin-bottom:4px}
.serve-lists li::before{content:"• "}
.email{margin-top:6px;width:156px;height:23px;background:#fff;border-radius:2px;font-size:9px;color:#aaa;padding:6px 9px}
.subscribe{margin-top:7px;display:inline-block;background:var(--gold);color:#332800;font-size:9px;padding:6px 13px;border-radius:2px}
.footer__social{display:flex;gap:7px;margin-top:10px}
.footer__social span{width:22px;height:22px;border-radius:50%;background:#8b84d4;display:block}
.footer__rule{position:absolute;left:68px;right:68px;top:153px;height:1px;background:rgba(255,255,255,.12)}
.copyright{position:absolute;top:166px;width:100%;text-align:center;font-size:8px;color:#b9b5ea}
</style>
</head>
<body>

<div class="topbar">
  <p class="topbar__tagline">A house of prayer for all nations, where the love, the presence and the power of God are real.</p>
  <div class="schedule">
    <span class="schedule__label">SUNDAY SERVICE SCHEDULE</span>
    <span class="schedule__times">09:00 A.M. | Sunday School<br>10:30 A.M. | Convergent Service</span>
  </div>
</div>

<header class="header">
  <a class="brand" href="#"><span class="brand__dot"></span><span class="brand__name">Harvest Gateway Fellowship Ministries</span></a>
  <div class="info info--donate"><h3>Donate</h3>Lorem Ipsum is simply dummy text of the printing<a class="more" href="#">Donate Now »</a></div>
  <span class="divider" style="left:405px"></span>
  <div class="info info--prayer"><h3>Request Prayer</h3>Lorem Ipsum is simply dummy text of the printing and typesetting industry.<a class="more" href="#">Request Now »</a></div>
  <span class="divider" style="left:598px"></span>
  <div class="info info--address"><h3>Address</h3>Harvest Gateway<br>City, Location<a class="more" href="#">Contact »</a></div>
  <span class="divider" style="left:719px"></span>
  <div class="social"><span aria-label="Social link"></span><span aria-label="Social link"></span></div>
</header>

<nav class="nav">
  <a href="#">Home</a><a href="#">About</a><a href="#">Staff Profile</a><a href="#">News and Events</a><a href="#">Worship &amp; Services</a><a href="#">Groups</a><a href="#">Shop</a><a href="#">Resources</a><a href="#">Contact</a>
</nav>

<section class="banner" role="img" aria-label="Golden wheat field banner">
  <p class="crumbs">Home &gt; Resource Center</p>
  <h1>Resource Center</h1>
</section>

<div class="filter">
  <span class="filter__label">Filter by</span>
  <a class="active" href="#">All</a><a href="#">Sunday Sermon</a><a href="#">Radio Shows</a><a href="#">Bible Study</a><a href="#">Videos</a>
</div>

<div class="column column--left">
  <article class="card card--audio">
    <div class="player"><span class="player__play"></span><span class="player__track"></span><span class="player__vol"></span><span class="player__volbar"></span></div>
    <div class="card__body"><h3 class="card__title">Sunday Sermon</h3><p class="card__type">Audio</p><p class="card__text">Lorem Ipsum is simply dummy text of the print-ing and typesetting industry lorem Ipsum has been the industry's standard dummy text.</p></div>
    <div class="card__foot"><span>31-Jul-14</span><span class="share">Share <i></i><i></i></span></div>
  </article>
  <article class="card card--audio">
    <div class="player"><span class="player__play"></span><span class="player__track"></span><span class="player__vol"></span><span class="player__volbar"></span></div>
    <div class="card__body"><h3 class="card__title">Radio Show</h3><p class="card__type">Audio</p><p class="card__text">Lorem Ipsum is simply dummy text of the print-ing and typesetting industry lorem Ipsum has been the industry's standard dummy text.</p></div>
    <div class="card__foot"><span>21-Jul-14</span><span class="share">Share <i></i><i></i></span></div>
  </article>
  <article class="card card--video">
    <div class="card__media" role="img" aria-label="Video still of a purple evening sky with a setting sun"></div>
    <div class="player"><span class="player__play"></span><span class="player__track"></span><span class="player__vol"></span><span class="player__volbar"></span></div>
    <div class="card__body"><h3 class="card__title">I Surrender All</h3><p class="card__artist">Jonah Whitfield</p><p class="card__text">A worship song we play for worship at out church. I have put this is video format for that purpose. All rights reserved to the artist.</p></div>
    <div class="card__foot"><span>06-Jul-14</span><span class="share"><i></i><i></i></span></div>
  </article>
</div>

<div class="column column--right">
  <article class="card card--video">
    <div class="card__media" role="img" aria-label="Video still of a purple evening sky with a setting sun"></div>
    <div class="player"><span class="player__play"></span><span class="player__track"></span><span class="player__vol"></span><span class="player__volbar"></span></div>
    <div class="card__body"><h3 class="card__title">I Surrender All</h3><p class="card__artist">Jonah Whitfield</p><p class="card__text">A worship song we play for worship at out church. I have put this is video format for that purpose. All rights reserved to the artist.</p></div>
    <div class="card__foot"><span>26-Jul-14</span><span class="share"><i></i><i></i></span></div>
  </article>
  <article class="card card--audio">
    <div class="player"><span class="player__play"></span><span class="player__track"></span><span class="player__vol"></span><span class="player__volbar"></span></div>
    <div class="card__body"><h3 class="card__title">Bible Study</h3><p class="card__type">Audio</p><p class="card__text">Lorem Ipsum is simply dummy text of the print-ing and typesetting industry lorem Ipsum has been the industry's standard dummy text.</p></div>
    <div class="card__foot"><span>16-Jul-14</span><span class="share">Share <i></i><i></i></span></div>
  </article>
  <article class="card card--audio">
    <div class="player"><span class="player__play"></span><span class="player__track"></span><span class="player__vol"></span><span class="player__volbar"></span></div>
    <div class="card__body"><h3 class="card__title">Sunday Sermon</h3><p class="card__type">Audio</p><p class="card__text">Lorem Ipsum is simply dummy text of the print-ing and typesetting industry lorem Ipsum has been the industry's standard dummy text.</p></div>
    <div class="card__foot"><span>03-Jul-14</span><span class="share">Share <i></i><i></i></span></div>
  </article>
</div>

<aside class="archive">
  <h2>RADIO SHOW ARCHIVE</h2>
  <ul>
    <li class="current">Jul 2014 <span>(24)</span></li>
    <li>Jun 2014 <span>(18)</span></li>
    <li>May 2014 <span>(19)</span></li>
    <li>Apr 2014 <span>(34)</span></li>
    <li>Mar 2014 <span>(54)</span></li>
    <li>Feb 2014 <span>(29)</span></li>
    <li style="border-bottom:0">Jan 2014 <span>(19)</span></li>
  </ul>
</aside>

<footer class="footer">
  <div class="footer__col footer__col--contact">
    <h4>CONTACT US</h4>
    <p>Harvest Gateway<br>Location, city<br>State Name, Country</p>
    <p class="contact-line" style="margin-top:8px"><svg width="10" height="10" viewBox="0 0 10 10"><path d="M2 1l2 2-1 1.2c.6 1.2 1.6 2.2 2.8 2.8L7 6l2 2-1.3 1.3C4.5 9 1 5.5.7 2.3z" fill="#cfcdf0"/></svg>+1 555-014-2290</p>
    <p class="contact-line" style="margin-top:2px"><svg width="10" height="8" viewBox="0 0 10 8"><rect x=".5" y=".5" width="9" height="7" fill="none" stroke="#cfcdf0"/><path d="M.5.5L5 4.5 9.5.5" fill="none" stroke="#cfcdf0"/></svg>hello@harvestgateway.org</p>
  </div>
  <div class="footer__col footer__col--serve">
    <h4>COMMUNITIES WE SERVE</h4>
    <div class="serve-lists">
      <ul><li>Lorem Ipsum</li><li>Dummy Links</li><li>More dummy</li><li>Sample Text</li><li>More samples</li></ul>
      <ul><li>type text dummy</li><li>Lorem Ipsum</li></ul>
    </div>
  </div>
  <div class="footer__col footer__col--news">
    <h4>NEWSLETTER</h4>
    <p>Enter your email below to get notified</p>
    <div class="email">Your Email</div>
    <a class="subscribe" href="#">Subscribe</a>
  </div>
  <div class="footer__col footer__col--connect">
    <h4>CONNECT WITH US</h4>
    <p>Stay connected for the latest updates at Harvest Gateway Fellowship</p>
    <div class="footer__social"><span></span><span></span></div>
  </div>
  <div class="footer__rule"></div>
  <p class="copyright">Copyright © 2014. All rights reserved. Harvest Gateway.</p>
</footer>

</body>
</html>
```